Brimsett Gardening Fresh New Website

We are looking to create a simple fresh website for our landscaping business. The website should appeal to a 'high end' audience. We deal with a lot of Embassies and affluent clients who have extremely large gardens that are meticulously maintained. The site is about communicating our excellent landscaping and customer service skills and encouraging new clients to reach out and engage us to take care of their gardens.

The website is basically going to be our business card, it will have almost no functionality other than two 'contact us' forms, one for smaller clients and one for more detailed projects.

The website will not have a lot of written content and will have to show photos of beautifully landscaped gardens.

The main logo in black will influence the site, however, we are open to all suggestions.

We are expecting to have the following pages:
Home Page
Services
About Us
Contact Us
Showcase (photo gallery of our work)

We need someone who can code it to wordpress and be available for minor changes over a number of days. They will be simple tweaks.

```html
<!DOCTYPE html>
<html lang="en">
<head>
<meta charset="utf-8">
<title>Brimsett Gardening</title>
<link href="https://fonts.googleapis.com/css2?family=Gelasio:wght@500;700&family=Roboto:wght@400;500;700&display=swap" rel="stylesheet">
<style>
:root{
  --ink:#141414;
  --black:#111111;
  --white:#ffffff;
  --gold:#b8862a;
  --gold-light:#f5d547;
  --gold-grad:linear-gradient(90deg,#b07f25 0%,#f5d547 100%);
  --text:#222222;
}
*{box-sizing:border-box;margin:0;padding:0}
html,body{width:1200px;height:3107px;overflow:hidden}
body{position:relative;background:var(--white);font-family:'Roboto',sans-serif;color:var(--text)}
.serif{font-family:'Gelasio',serif;font-weight:700}
.gold{color:var(--gold)}
.btn{position:absolute;background:var(--gold-grad);color:var(--black);font-weight:500;font-size:13px;display:flex;align-items:center;justify-content:center}

/* header */
.site-header{position:absolute;left:0;top:0;width:1200px;height:92px;background:var(--black);color:var(--white)}
.social{position:absolute;top:17px;left:141px;display:flex;gap:12px}
.social span{width:13px;height:13px;border:1.5px solid var(--white);border-radius:50%}
.nav a{position:absolute;top:58px;font-size:13px;color:var(--white);text-decoration:none}
.nav-rule{position:absolute;top:45px;left:141px;width:293px;height:1px;background:#555}
.brand{position:absolute;left:476px;top:44px;width:200px;text-align:center;color:var(--gold)}
.brand .mark{width:16px;height:16px;border:1.5px solid var(--gold);border-radius:50%;margin:-32px auto 6px}
.brand .name{font-family:'Gelasio',serif;font-weight:500;font-size:12px;letter-spacing:5px;line-height:14px}
.phone{position:absolute;top:17px;left:958px;font-size:13px;display:flex;gap:8px;align-items:center}

/* hero */
.hero{position:absolute;left:0;top:92px;width:1200px;height:564px;background:linear-gradient(180deg,#8a9298 0%,#6e7a6f 45%,#3f5a2c 75%,#2f4a22 100%)}
.hero-kicker{position:absolute;top:292px;width:1200px;text-align:center;color:var(--white);font-size:25px;letter-spacing:3px;font-weight:500}
.hero-title{position:absolute;top:330px;width:1200px;text-align:center;color:var(--white);font-size:50px;line-height:56px}

/* quote form */
.quote{position:absolute;left:693px;top:610px;width:372px;height:440px;background:var(--black);border:5px solid var(--gold)}
.quote h3{position:absolute;left:24px;top:22px;color:var(--white);font-size:21px;line-height:27px}
.field{position:absolute;left:24px;width:315px;height:35px;border:1px solid var(--white);color:var(--white);font-size:12.5px;padding:10px 14px}
.field i{color:#e33;font-style:normal}

/* about */
.about-title{position:absolute;left:141px;top:706px;font-size:38px;line-height:46px}
.about-text{position:absolute;left:141px;top:806px;width:445px;font-size:12.5px;line-height:22.5px;color:var(--text)}
.about-text p+p{margin-top:6px}

/* services */
.services-bg{position:absolute;left:0;top:1138px;width:1200px;height:336px;background:linear-gradient(180deg,#3d4a2a 0%,#5a6a3d 50%,#6f7b4a 100%)}
.section-title{position:absolute;width:1200px;text-align:center;font-size:38px}
.circle{position:absolute;width:268px;height:268px;border-radius:50%;border-bottom:7px solid var(--gold-light)}
.svc-label{position:absolute;width:300px;text-align:center;font-size:18px;top:1576px}

/* reviews */
.review{position:absolute;left:282px;top:1752px;width:635px;height:163px;border:1px solid var(--gold);border-top-left-radius:34px;text-align:center;font-size:12.5px;line-height:22.5px;padding:38px 50px 0}
.review .who{margin-top:8px;font-size:13.5px;font-weight:500;color:var(--black)}
.arrow{position:absolute;top:1833px;width:26px;height:26px}

/* cta */
.cta{position:absolute;left:0;top:2025px;width:1200px;height:432px;background:linear-gradient(180deg,#3b3b33 0%,#4b4a40 50%,#3a3732 100%)}
.cta-text{position:absolute;top:2215px;width:1200px;text-align:center;color:var(--white);font-size:12.5px;line-height:22.5px}

/* gallery */
.dark-band{position:absolute;left:0;top:2726px;width:1200px;height:346px;background:var(--black)}
.shot{position:absolute;top:2613px;width:175px;height:172px}

/* footer */
.f-brand{position:absolute;left:135px;top:2900px;width:160px;text-align:center;color:var(--gold)}
.f-brand .mark{width:34px;height:34px;border:2px solid var(--gold);border-radius:50%;margin:0 auto 18px}
.f-brand .name{font-family:'Gelasio',serif;font-weight:500;font-size:18px;letter-spacing:5px;line-height:24px}
.f-nav a{position:absolute;top:2888px;font-size:12.5px;color:var(--white);text-decoration:none}
.f-rule{position:absolute;left:404px;top:2931px;width:654px;height:1px;background:#444}
.f-item{position:absolute;top:2960px;display:flex;align-items:center;gap:12px;color:var(--white);font-size:12.5px;line-height:16px}
.f-icon{width:36px;height:36px;border-radius:50%;background:var(--gold-grad);display:flex;align-items:center;justify-content:center}
.bottom-bar{position:absolute;left:0;top:3072px;width:1200px;height:35px;background:var(--gold-grad);font-size:12px;color:var(--black)}
.bottom-bar .copy{position:absolute;left:141px;top:11px}
.bottom-bar .social{top:11px;left:993px}
.bottom-bar .social span{border-color:var(--black)}
</style>
</head>
<body>

<header class="site-header">
  <div class="social"><span></span><span></span><span></span></div>
  <div class="nav-rule"></div>
  <nav class="nav">
    <a style="left:141px">Home</a>
    <a style="left:246px">Services</a>
    <a style="left:367px">Gallery</a>
    <a style="left:714px">About Us</a>
    <a style="left:838px">Contact Us</a>
    <a style="left:971px">Projects For <svg width="12" height="8" viewBox="0 0 12 8"><path d="M1 1l5 5 5-5" fill="none" stroke="#fff" stroke-width="1.6"/></svg></a>
  </nav>
  <div class="brand"><div class="mark"></div><div class="name">BRIMSETT GARDENING</div></div>
  <div class="phone"><svg width="14" height="14" viewBox="0 0 24 24"><path d="M5 3h4l2 5-3 2a12 12 0 006 6l2-3 5 2v4a2 2 0 01-2 2A18 18 0 013 5a2 2 0 012-2z" fill="none" stroke="#fff" stroke-width="1.6"/></svg>123 456 7890</div>
</header>

<section class="hero" role="img" aria-label="Large grey house with manicured lawn and flowering shrubs"></section>
<div class="hero-kicker">LANDSCAPE PROS</div>
<h1 class="hero-title serif">Stunning Landscapes To<br>Inspire Your Family</h1>
<div class="btn" style="left:534px;top:453px;width:132px;height:33px">Request A Quote</div>

<form class="quote">
  <h3 class="serif"><span class="gold">24% Off</span> For New<br>Landscape Services</h3>
  <div class="field" style="top:83px">Name<i>*</i></div>
  <div class="field" style="top:125px">Email<i>*</i></div>
  <div class="field" style="top:167px">Phone Number<i>*</i></div>
  <div class="field" style="top:209px">Street Address &amp; Zip Code<i>*</i></div>
  <div class="field" style="top:251px">Which Service Would You Like A Bill For?
    <svg style="position:absolute;right:12px;top:13px" width="13" height="8" viewBox="0 0 13 8"><path d="M1 1l5.5 5.5L12 1" fill="none" stroke="#fff" stroke-width="1.6"/></svg></div>
  <div class="field" style="top:293px;height:70px">Message</div>
  <div class="btn" style="left:24px;top:373px;width:315px;height:35px">Request A Quote</div>
</form>

<h2 class="about-title serif">About<br><span class="gold">Brimsett Gardening</span></h2>
<div class="about-text">
  <p>Lorem Ipsum Is Simply Dummy Text Of The Printing And Typesetting Industry. Lorem Ipsum Has Been The Industry's Standard Dummy Text Ever Since The 1500s, When An Unknown Printer Took A Galley Of Type And Scrambled It To Make A Type Specimen Book.</p>
  <p>Lorem Ipsum Is Simply Dummy Text Of The Printing And Typesetting Industry. Lorem Ipsum Has Been The Industry's Standard Dummy Text Ever Since The 1500s, When &nbsp;And Scrambled It To Make A Type Specimen Book.</p>
</div>
<div class="btn" style="left:141px;top:988px;width:94px;height:35px">Read More</div>

<section class="services-bg" role="img" aria-label="Park lawn with wooden pavilion and trees"></section>
<h2 class="section-title serif" style="top:1212px;color:var(--white)">Our <span class="gold">Services</span></h2>
<div class="circle" role="img" aria-label="Green lawn with colourful flowering bushes" style="left:145px;top:1285px;background:linear-gradient(180deg,#8fb36a 0%,#c77a5a 45%,#4fa52f 70%,#3e8f25 100%)"></div>
<div class="circle" role="img" aria-label="Patio with outdoor sofa set" style="left:465px;top:1285px;border-bottom-color:var(--gold);background:linear-gradient(180deg,#9aa58a 0%,#c9ced0 35%,#d8cfc0 70%,#b9a98d 100%)"></div>
<div class="circle" role="img" aria-label="Gloved hands spraying weeds among leaves" style="left:787px;top:1285px;background:linear-gradient(180deg,#3f6a34 0%,#5d8a4a 50%,#2d4f2a 100%)"></div>
<div class="svc-label serif" style="left:129px">Lawn Fertilizing</div>
<div class="svc-label serif gold" style="left:449px">Patios</div>
<div class="svc-label serif" style="left:771px">Weed Control</div>

<h2 class="section-title serif" style="top:1674px">Customer <span class="gold">Reviews</span></h2>
<svg class="arrow" style="left:228px" viewBox="0 0 26 26"><circle cx="13" cy="13" r="12" fill="none" stroke="#111" stroke-width="1.6"/><path d="M15 8l-5 5 5 5" fill="none" stroke="#111" stroke-width="1.6"/></svg>
<div class="review">Lorem Ipsum Is Simply Dummy Text Of The Printing And Typesetting Industry. Lorem Ipsum Has Been The Industry's Standard Dummy Text Ever Since The 1500s, When An Unknown Printer Took A Galley Of Type And Scrambled It To Make A Type Specimen Book.<div class="who">– Henrik. D</div></div>
<svg class="arrow" style="left:945px" viewBox="0 0 26 26"><circle cx="13" cy="13" r="12" fill="none" stroke="#111" stroke-width="1.6"/><path d="M11 8l5 5-5 5" fill="none" stroke="#111" stroke-width="1.6"/></svg>

<section class="cta" role="img" aria-label="Covered terrace with outdoor sofas and plants"></section>
<h2 class="section-title serif" style="top:2160px;color:var(--white)">Build Your Outdoor Dream With Us</h2>
<div class="cta-text">Lorem Ipsum Is Simply Dummy Text Of The Printing And Typesetting Industry. Lorem Ipsum Has Been The Industry's Standard Dummy<br>Text Ever Since The 1500s, When An Unknown Printer Took A Galley Of Type And Scrambled It To Make A Type Specimen Book.</div>
<div class="btn" style="left:551px;top:2279px;width:98px;height:34px">Contact Us</div>

<h2 class="section-title serif" style="top:2533px">Work <span class="gold">Gallery</span></h2>
<div class="dark-band"></div>
<div class="shot" role="img" aria-label="Golf course fairway with pine trees" style="left:141px;background:linear-gradient(180deg,#6b8a5a,#8fb04a 60%,#7aa03a)"></div>
<div class="shot" role="img" aria-label="Hand holding a grass sprout" style="left:327px;background:linear-gradient(135deg,#a9c98a,#6a9a45)"></div>
<div class="shot" role="img" aria-label="Hay bale on a green field" style="left:512px;background:linear-gradient(180deg,#8aa04a,#7a7a60 50%,#6f8f35)"></div>
<div class="shot" role="img" aria-label="Brick path through a green park" style="left:697px;background:linear-gradient(180deg,#9ec3d8,#5f9a3a 45%,#a05a4a)"></div>
<div class="shot" role="img" aria-label="Worker laying turf rolls on soil" style="left:883px;background:linear-gradient(180deg,#7aa04a,#8a7a6a 55%,#9a8d80)"></div>

<div class="f-brand"><div class="mark"></div><div class="name">BRIMSETT GARDENING</div></div>
<nav class="f-nav">
  <a style="left:404px">Home</a>
  <a style="left:509px">Services</a>
  <a style="left:629px">Gallery</a>
  <a style="left:739px">About Us</a>
  <a style="left:862px">Project Me</a>
  <a style="left:994px">Contact Us</a>
</nav>
<div class="f-rule"></div>
<div class="f-item" style="left:401px"><div class="f-icon"><svg width="16" height="18" viewBox="0 0 16 18"><path d="M8 17s6-6 6-10A6 6 0 002 7c0 4 6 10 6 10z" fill="none" stroke="#111" stroke-width="1.5"/><circle cx="8" cy="7" r="2" fill="none" stroke="#111" stroke-width="1.5"/></svg></div><span>123, Street Name, City<br>Name, Country Name, &nbsp;1234</span></div>
<div class="f-item" style="left:659px"><div class="f-icon"><svg width="16" height="16" viewBox="0 0 24 24"><path d="M5 3h4l2 5-3 2a12 12 0 006 6l2-3 5 2v4a2 2 0 01-2 2A18 18 0 013 5a2 2 0 012-2z" fill="none" stroke="#111" stroke-width="1.8"/></svg></div><span>123 456 7890</span></div>
<div class="f-item" style="left:842px"><div class="f-icon"><svg width="16" height="12" viewBox="0 0 16 12"><rect x="1" y="1" width="14" height="10" fill="none" stroke="#111" stroke-width="1.5"/><path d="M1 1l7 6 7-6" fill="none" stroke="#111" stroke-width="1.5"/></svg></div><span>hello@brimsettgardens.com</span></div>

<footer class="bottom-bar">
  <div class="copy">© 2024 Brimsett Gardening. All Rights Reserved.</div>
  <div class="social"><span></span><span></span><span></span></div>
</footer>

</body>
</html>
```